75%-100% OFF - Insulation Banner Design

Need banners created for an online marketing push for my insulation business Tivoran Energy.

www.tivoranenergy.com

Specifically - I would like the banners to pop utilizing our colors in neon. To see samples of colors we use - visit our asset folder.

https://files.quelmarsh.net/share/7kXpw20LmzQaRt5vYbNe83HsUd4cJf?view=open

I will attach sample files to this project.

The banner must highlight 75%-100% off Insulation and Weatherization. If you can include our current perfect Starlist reviews somewhere in the advertisement that would be awesome but not a requirement.

The banner must meet Hearthwise logo guidelines. Please see attachment.

Target Market(s)

Home Owners

Industry/Entity Type

Insulation and Construction

Font styles to use
Sans Serif

Colors
59FF00
82FF00
B8FF75
E3FFCB
F4FFEA

Requirements
Must have
• Hearthwise Logo per project description. Must have 75-100% off somewhere that is very clear. And must have our company Tivoran Energy Logo.
Nice to have
• Tivoran Energy Logo

```html
<!DOCTYPE html>
<html lang="en">
<head>
<meta charset="utf-8">
<title>Tivoran Energy – Insulation Banner</title>
<link rel="stylesheet" href="https://fonts.googleapis.com/css2?family=Anton&family=Bebas+Neue&family=Montserrat:wght@600;700&display=swap">
<style>
  :root {
    --sky: #08c6fa;
    --leaf: #2fc80c;
    --leaf-deep: #3ad608;
    --neon-1: #59ff00;
    --neon-2: #82ff00;
    --neon-3: #b8ff75;
    --neon-4: #e3ffcb;
    --neon-5: #f4ffea;
    --forest: #14530a;
    --orange: #ff7a00;
    --moss: #4f9a2e;
    --white: #ffffff;
    --dusk: #4d5f8e;
    --lawn: #3f6a34;
    --timber: #c7996a;
    --fluff: #ece3d6;
  }
  * { margin: 0; padding: 0; box-sizing: border-box; }
  html, body { width: 1200px; height: 625px; overflow: hidden; background: var(--white); }
  .banner {
    position: relative;
    width: 1200px;
    height: 625px;
    overflow: hidden;
    background: linear-gradient(180deg, var(--sky) 0%, #16cf9a 28%, var(--leaf) 60%, var(--leaf-deep) 100%);
    font-family: "Montserrat", sans-serif;
    color: var(--white);
  }
  .brand {
    position: absolute;
    left: 32px;
    top: 38px;
    font-weight: 700;
    font-size: 44px;
    line-height: 1;
    color: var(--white);
    letter-spacing: 1px;
  }
  .phone {
    position: absolute;
    right: 22px;
    top: 14px;
    font-family: "Bebas Neue", sans-serif;
    font-size: 70px;
    line-height: 1;
    letter-spacing: 1px;
    color: var(--white);
  }
  .offer {
    position: absolute;
    left: 26px;
    top: 106px;
    height: 62px;
    padding: 0 22px;
    border-radius: 31px;
    background: linear-gradient(90deg, var(--neon-1), var(--neon-2));
    border: 3px solid var(--neon-5);
    box-shadow: 0 0 18px var(--neon-3), 0 0 4px var(--neon-4);
    font-family: "Anton", sans-serif;
    font-size: 40px;
    line-height: 56px;
    letter-spacing: 0.5px;
    color: var(--forest);
    white-space: nowrap;
  }
  .headline {
    position: absolute;
    left: 24px;
    top: 182px;
    font-family: "Anton", sans-serif;
    font-weight: 400;
    line-height: 1;
    text-transform: uppercase;
  }
  .headline span {
    display: block;
    font-size: 88px;
    height: 103px;
    letter-spacing: -2px;
    -webkit-text-stroke: 5px var(--white);
    paint-order: stroke fill;
  }
  .headline .orange { color: var(--orange); }
  .headline .moss { color: var(--moss); }
  .website {
    position: absolute;
    left: 30px;
    top: 563px;
    font-family: "Anton", sans-serif;
    font-size: 22px;
    line-height: 1;
    color: var(--white);
  }
  .reviews {
    position: absolute;
    left: 228px;
    top: 538px;
    color: var(--white);
  }
  .reviews .prompt {
    font-weight: 700;
    font-size: 11.5px;
    letter-spacing: 0.2px;
  }
  .reviews .prompt b { font-size: 13px; letter-spacing: 1px; }
  .reviews .platform {
    font-weight: 600;
    font-size: 42px;
    line-height: 1.05;
  }
  .partner {
    position: absolute;
    left: 424px;
    top: 568px;
    font-weight: 700;
    font-size: 30px;
    line-height: 1;
    color: var(--white);
  }
  .collage {
    position: absolute;
    left: 0;
    top: 0;
  }
</style>
</head>
<body>
<main class="banner">
  <div class="brand">Tivoran Energy</div>
  <div class="phone">555-014-2290</div>

  <div class="offer">75%–100% OFF</div>

  <h1 class="headline">
    <span class="orange">Insulation</span>
    <span class="moss">Weatherization</span>
    <span class="orange">Energy Savings</span>
  </h1>

  <div class="website">tivoranenergy.com</div>

  <div class="reviews">
    <div class="prompt">Review us on <b>★★★★★</b></div>
    <div class="platform">Starlist</div>
  </div>

  <div class="partner">Hearthwise</div>

  <svg class="collage" width="1200" height="625" viewBox="0 0 1200 625">
    <defs>
      <linearGradient id="houseTone" x1="0" y1="0" x2="0" y2="1">
        <stop offset="0" stop-color="#6f86b8"/>
        <stop offset="0.55" stop-color="#4d5f8e"/>
        <stop offset="1" stop-color="#3f6a34"/>
      </linearGradient>
      <linearGradient id="atticTone" x1="0" y1="0" x2="1" y2="1">
        <stop offset="0" stop-color="#c7996a"/>
        <stop offset="1" stop-color="#ece3d6"/>
      </linearGradient>
      <linearGradient id="foamTone" x1="0" y1="0" x2="1" y2="1">
        <stop offset="0" stop-color="#e6d2a4"/>
        <stop offset="1" stop-color="#b58c5e"/>
      </linearGradient>
      <linearGradient id="floorTone" x1="0" y1="0" x2="1" y2="1">
        <stop offset="0" stop-color="#8a6140"/>
        <stop offset="1" stop-color="#c9a078"/>
      </linearGradient>
    </defs>

    <g role="img" aria-label="Photo of a craftsman-style house at dusk with lit windows and a stone path">
      <polygon fill="url(#houseTone)" points="627,159 769,159 841,284 769,409 627,409 555,284"/>
    </g>
    <g role="img" aria-label="Photo of a worker blowing loose-fill insulation into an attic">
      <polygon fill="url(#atticTone)" points="663,422 771,422 825,516 771,609 663,609 609,516"/>
    </g>
    <g role="img" aria-label="Photo of insulation being sprayed between attic rafters">
      <polygon fill="url(#atticTone)" points="835,322 943,322 997,416 943,509 835,509 781,416"/>
    </g>
    <g role="img" aria-label="Photo of spray foam insulation on attic walls and framing">
      <polygon fill="url(#foamTone)" points="1007,219 1115,219 1169,313 1115,406 1007,406 953,313"/>
    </g>
    <g role="img" aria-label="Photo of an attic hatch with sealed wooden floorboards">
      <polygon fill="url(#floorTone)" points="1007,422 1115,422 1169,516 1115,609 1007,609 953,516"/>
    </g>

    <polygon fill="#ff7a00" points="835,522 943,522 997,616 943,709 835,709 781,616"/>
    <polygon fill="#f4ffea" points="1179,322 1287,322 1341,416 1287,509 1179,509 1125,416"/>
    <polygon fill="#ff7a00" points="1179,525 1287,525 1341,619 1287,712 1179,712 1125,619"/>
  </svg>
</main>
</body>
</html>
```